BLS Business Card 2018

Larkmere Chiropractic. We have two locations that we want to advertise on the same card. Brightvale OrthoCore campus address: 3815 Pellham Dr., Suite 240, Flowood, MS 39417. Madison address: 246 Willowmere Dr., Building D., Madison, MS 39284. website: www.drlarkmere-example.com. o:(601)555-0147 f:(601)555-0183

Target Market(s)

Health care decision makers: primary care doctors and mothers

Contact Information for Business Card

I have no idea; up for any suggestions and I'd do much better picking from examples versus describing what I'm looking for. We are in a very high end location and would like the cards to look really sharp.

Requirements
Must have
• My name, Martin R Belvane, D.C.

```html
<!DOCTYPE html>
<html lang="en">
<head>
<meta charset="utf-8">
<title>Larkmere Chiropractic – Business Card</title>
<link rel="stylesheet" href="https://fonts.googleapis.com/css2?family=Roboto+Condensed:wght@400;700&family=Tinos&display=swap">
<style>
  :root{
    --backdrop:#e8e5e0;
    --card:#ffffff;
    --ink:#1a1a1a;
    --ink-soft:#555555;
    --rule:#222222;
    --shadow:rgba(0,0,0,.14);
    --sketch-a:#f1f1f1;
    --sketch-b:#e2e2e2;
  }
  *{margin:0;padding:0;box-sizing:border-box}
  html,body{width:1200px;height:911px;overflow:hidden}
  body{
    background:var(--backdrop);
    font-family:"Roboto Condensed",Arial,sans-serif;
    color:var(--ink);
    display:flex;align-items:center;justify-content:center;gap:48px;
  }
  .card{
    width:546px;height:312px;background:var(--card);
    box-shadow:0 6px 18px var(--shadow);
    position:relative;overflow:hidden;
  }
  /* contact side */
  .figure-art{
    position:absolute;left:34px;top:120px;width:200px;height:170px;
    background:radial-gradient(ellipse at 50% 45%,var(--sketch-b),var(--sketch-a) 70%,transparent 100%);
    border-radius:40% 40% 30% 30%;
  }
  .contact-side .details{
    position:absolute;left:255px;top:34px;width:262px;
  }
  .holder-name{
    font-weight:700;font-size:20px;letter-spacing:.2px;text-transform:uppercase;
    padding-bottom:9px;border-bottom:2px solid var(--rule);
  }
  .location{
    margin-top:14px;font-size:13.5px;line-height:1.35;color:var(--ink-soft);
  }
  .location + .location{margin-top:8px}
  .lines{list-style:none;margin-top:12px;font-size:13.5px;line-height:1.5;color:var(--ink-soft)}
  .lines li{display:flex;align-items:center;gap:8px}
  .lines svg{width:12px;height:12px;flex:none;fill:var(--ink)}
  /* brand side */
  .brand-side .brand{
    position:absolute;left:150px;top:96px;
    font-family:"Tinos","Times New Roman",serif;font-weight:400;color:var(--ink);
    text-transform:uppercase;line-height:1;
  }
  .brand-line{display:block}
  .brand-line.primary{font-size:44px;letter-spacing:1px}
  .brand-line.secondary{font-size:25px;letter-spacing:1.5px;margin-top:2px}
  .brand-side .web{
    position:absolute;left:0;right:0;top:232px;text-align:center;
    font-size:13px;letter-spacing:5px;text-transform:uppercase;color:var(--ink-soft);
  }
</style>
</head>
<body>
  <section class="card contact-side">
    <div class="figure-art" role="img" aria-label="Fine line sketch of a human back and shoulders"></div>
    <div class="details">
      <h1 class="holder-name">Martin R Belvane, D.C.</h1>
      <p class="location">Brightvale OrthoCore campus :<br>3815 Pellham Dr., Suite 240<br>Flowood, MS 39417.</p>
      <p class="location">Madison address:<br>246 Willowmere Dr., Building D.<br>Madison, MS 39284.</p>
      <ul class="lines">
        <li><svg viewBox="0 0 24 24" aria-hidden="true"><path d="M6.6 10.8a15 15 0 0 0 6.6 6.6l2.2-2.2c.3-.3.7-.4 1-.2 1.1.4 2.3.6 3.6.6.6 0 1 .4 1 1V20c0 .6-.4 1-1 1A17 17 0 0 1 3 4c0-.6.4-1 1-1h3.5c.6 0 1 .4 1 1 0 1.3.2 2.5.6 3.6.1.3 0 .7-.2 1z"/></svg>(601)555-0147</li>
        <li><svg viewBox="0 0 24 24" aria-hidden="true"><path d="M6 2h9v6H6zM3 9h18v10H3zM6 14h12v8H6z"/></svg>(601)555-0183</li>
        <li><svg viewBox="0 0 24 24" aria-hidden="true"><circle cx="12" cy="12" r="10"/></svg>www.drlarkmere-example.com</li>
      </ul>
    </div>
  </section>

  <section class="card brand-side">
    <p class="brand">
      <span class="brand-line primary">Larkmere</span>
      <span class="brand-line secondary">Chiropractic</span>
    </p>
    <p class="web">www.drlarkmere-example.com</p>
  </section>
</body>
</html>
```